Veltrano.co - Polar Expeditions Specialists

We need a modern, visually striking business card for Veltrano.co, a company specialized in selling expedition cruises to the most remote regions on Earth, with a focus on the Arctic and Antarctica. The design should instantly communicate that the cardholder is an expert in polar travel. Use clean, premium aesthetics with cool tones like icy blue and white, possibly incorporating polar imagery (ice, glaciers, penguins, etc.)

Attached the logo

Contact Information for Business Card

Feels high-end and trustworthy.. Visually memorable — encourages people to keep it

Colors
0054AA
0677BA
7BADD7
CADEEF
E8F1F8

Requirements
Must have
• ice, glaciers, penguins, montains
Nice to have
• modern, transparente,

```html
<!DOCTYPE html>
<html lang="en">
<head>
<meta charset="utf-8">
<title>Veltrano.co Business Card</title>
<link rel="stylesheet" href="https://fonts.googleapis.com/css2?family=Poppins:wght@400;600;700&display=swap">
<style>
  :root {
    --brand-blue: #3677b8;
    --deep-blue: #1f3a73;
    --ice-blue: #7badd7;
    --pale-ice: #cadeef;
    --white: #ffffff;
    --text-grey: #4a4a4a;
    --backdrop: #d6d6d4;
  }
  * { box-sizing: border-box; margin: 0; padding: 0; }
  html, body { width: 1200px; height: 791px; overflow: hidden; }
  body {
    background: var(--backdrop);
    font-family: "Poppins", sans-serif;
    display: flex;
    align-items: center;
    justify-content: center;
    gap: 40px;
  }
  .card {
    width: 540px;
    height: 309px;
    position: relative;
    overflow: hidden;
    box-shadow: 0 8px 22px rgba(0,0,0,0.18);
  }

  /* Front */
  .card-front {
    background: var(--white);
    border-bottom: 4px solid var(--brand-blue);
    display: flex;
    align-items: center;
  }
  .brand-block {
    width: 290px;
    flex: none;
    padding-left: 34px;
    padding-right: 26px;
    display: flex;
    align-items: center;
    gap: 10px;
    align-self: flex-end;
    margin-bottom: 62px;
  }
  .brand-dot {
    width: 14px; height: 14px;
    border-radius: 50%;
    background: var(--brand-blue);
    flex: none;
  }
  .brand-name {
    font-weight: 700;
    font-size: 30px;
    color: var(--brand-blue);
    line-height: 1;
    white-space: nowrap;
  }
  .brand-tagline {
    font-size: 9.5px;
    font-weight: 600;
    color: var(--brand-blue);
    margin-top: 5px;
    white-space: nowrap;
  }
  .divider {
    width: 1.5px;
    height: 110px;
    background: var(--brand-blue);
    flex: none;
  }
  .contact-block { padding-left: 28px; }
  .person-name {
    font-weight: 700;
    font-size: 18px;
    color: var(--brand-blue);
    text-transform: uppercase;
    line-height: 1.1;
    white-space: nowrap;
  }
  .person-title {
    font-size: 13px;
    color: var(--text-grey);
    margin-bottom: 16px;
  }
  .contact-list { list-style: none; }
  .contact-item {
    display: flex;
    align-items: center;
    gap: 8px;
    font-size: 13px;
    color: var(--text-grey);
    line-height: 1.7;
    white-space: nowrap;
  }
  .contact-icon { width: 11px; height: 11px; fill: var(--brand-blue); flex: none; }

  /* Back */
  .card-back { background: var(--brand-blue); }
  .polar-artwork {
    position: absolute;
    left: 40px;
    bottom: 0;
    width: 300px;
    height: 285px;
    border-radius: 140px 140px 0 0;
    background: linear-gradient(120deg, var(--deep-blue) 0%, #2a4f8a 40%, var(--ice-blue) 100%);
  }
  .back-brand {
    position: absolute;
    right: 36px;
    bottom: 62px;
    text-align: left;
    color: var(--white);
  }
  .back-brand .brand-name { color: var(--white); font-size: 44px; }
  .back-brand .brand-tagline { color: var(--white); font-size: 13px; }
</style>
</head>
<body>

  <section class="card card-front">
    <div class="brand-block">
      <span class="brand-dot"></span>
      <div>
        <div class="brand-name">Veltrano.co</div>
        <div class="brand-tagline">Polar Expeditions Specialists</div>
      </div>
    </div>
    <div class="divider"></div>
    <div class="contact-block">
      <div class="person-name">Marcus Lindqvist</div>
      <div class="person-title">President</div>
      <ul class="contact-list">
        <li class="contact-item">
          <svg class="contact-icon" viewBox="0 0 24 24"><path d="M6.6 10.8a15.1 15.1 0 0 0 6.6 6.6l2.2-2.2a1 1 0 0 1 1-.25 11.4 11.4 0 0 0 3.6.57 1 1 0 0 1 1 1V20a1 1 0 0 1-1 1A17 17 0 0 1 3 4a1 1 0 0 1 1-1h3.5a1 1 0 0 1 1 1c0 1.25.2 2.45.57 3.6a1 1 0 0 1-.25 1z"/></svg>
          555-310-7824
        </li>
        <li class="contact-item">
          <svg class="contact-icon" viewBox="0 0 24 24"><path d="M2 5h20v14H2z M2 5l10 8 10-8" /></svg>
          marcus@veltrano.co
        </li>
        <li class="contact-item">
          <svg class="contact-icon" viewBox="0 0 24 24"><circle cx="12" cy="12" r="10"/></svg>
          www.veltrano.co
        </li>
      </ul>
    </div>
  </section>

  <section class="card card-back">
    <div class="polar-artwork" role="img" aria-label="Illustration of a polar bear silhouette with two penguins and stars in deep to icy blue tones"></div>
    <div class="back-brand">
      <div class="brand-name">Veltrano.co</div>
      <div class="brand-tagline">Polar Expeditions Specialists</div>
    </div>
  </section>

</body>
</html>
```